Global Beard Oil Review Business needs a refresh

topwhiskertonic.net is a global business who's mission is to curate all available beard oils from around the world, review and grade them and present this curated collection to the user of the website.

The scope of this job includes the web site design and the design of a suitable logo to be used in the site header.

The existing site can be seen on http://topwhiskertonic.net, however this is a mock-up only the style and logo should NOT be used. This is to give you an idea of the concept of the site only.

This job is for PSD design only.

See attached design brief for detailed design requirements.
Updates

Project Deadline Extended
Reason: Extending deadline by 5 days to allow for final submissions

Target Market(s)

Men's grooming / retail

Industry/Entity Type

Retail

Number of Pages Required

2 page

Font styles to use
Sans Serif

Requirements
Must have
• 1) Comparison Table
• 2) Side Bar
• 3) Header area
• 4) Photo of Delvin Marsk (attached - can be circular or "cut-out")
• 5) Cool beard-oriented custom design background (e.g., stylistic black/brown on brown/orange beard background. I envision this beard background "drawing" rather than photo based)
• (see attached design requirements for details)
Nice to have
• Signature style writing at top with name "Delvin Marsk"
Should not have
• Do NOT use the look & feel or logo from the existing site.

```html
<!DOCTYPE html>
<html lang="en">
<head>
<meta charset="utf-8">
<title>Top Whisker Tonic – Beard Oil Reviews</title>
<link href="https://fonts.googleapis.com/css2?family=Lato:wght@400;700;900&display=swap" rel="stylesheet">
<style>
:root{
  --orange:#f7941d;
  --ink:#2b2b2b;
  --panel:rgba(222,222,222,.93);
  --row:rgba(150,150,150,.85);
  --head:rgba(120,120,120,.9);
  --side:#3b3b3b;
  --side-dark:#2f2f2f;
  --footer:rgba(40,40,40,.92);
  --white:#ffffff;
  --muted:#cfcfcf;
}
*{margin:0;padding:0;box-sizing:border-box}
html,body{width:1200px;height:802px;overflow:hidden}
body{position:relative;font-family:'Lato',sans-serif;color:var(--ink);background:#555}
.hero-photo{position:absolute;left:0;top:0;width:1200px;height:222px;
  background:radial-gradient(ellipse at 50% 60%,#6b6b6b 0%,#3e3e3e 45%,#262626 100%)}
.beard-photo{position:absolute;left:0;top:222px;width:1200px;height:452px;
  background:linear-gradient(90deg,#8d8d8d 0%,#5a5a5a 25%,#3a3a3a 50%,#6a6a6a 75%,#9a9a9a 100%)}
.brand{position:absolute;left:0;top:60px;width:1200px;text-align:center}
.brand-mark{display:inline-block;width:22px;height:22px;border-radius:50%;background:var(--orange);vertical-align:middle;margin-right:10px}
.brand-name{font-weight:900;font-size:30px;color:var(--orange);vertical-align:middle;letter-spacing:.5px}
.main-nav{position:absolute;top:180px;left:0;width:1200px;height:42px}
.main-nav a{position:absolute;top:0;font-size:19px;font-weight:700;font-variant:small-caps;color:var(--white);text-decoration:none;letter-spacing:.2px}
.main-nav a.active,.main-nav a.hover{color:var(--orange)}
.main-nav a.active::after{content:"";position:absolute;left:0;right:0;top:38px;height:2px;background:var(--orange)}
.review-panel{position:absolute;left:239px;top:258px;width:526px;height:379px;background:var(--panel)}
.review-panel h1{position:absolute;left:9px;top:18px;font-size:23px;font-weight:900;color:var(--ink)}
.review-panel .intro{position:absolute;left:9px;top:56px;width:505px;font-size:11px;line-height:18.5px;color:#333}
.compare{position:absolute;left:8px;top:110px;width:510px;border-collapse:collapse;font-size:8px;color:#333;table-layout:fixed}
.compare th{height:42px;background:var(--head);font-size:9.5px;font-weight:700;color:#3a3a3a;text-align:center}
.compare td{height:42px;text-align:center;vertical-align:middle}
.compare tbody tr:nth-child(even) td{background:var(--row)}
.compare td.num{font-size:10px}
.compare td.txt{text-align:left;padding-left:6px;line-height:10px}
.bottle{display:inline-block;width:12px;height:30px;border-radius:3px 3px 2px 2px;background:linear-gradient(#3a2a18,#b07a30)}
.bottle.dark{background:linear-gradient(#222,#444)}
.bottle.pale{background:linear-gradient(#9a8a70,#e0c9a0)}
.buy{display:inline-block;width:57px;height:18px;line-height:18px;background:var(--orange);color:var(--white);font-size:6.5px;font-weight:700;text-transform:uppercase}
.sidebar{position:absolute;left:775px;top:258px;width:184px;height:379px;background:var(--side)}
.author-photo{position:absolute;left:47px;top:14px;width:90px;height:90px;border-radius:50%;background:radial-gradient(circle,#9a9a9a,#4a4a4a)}
.author-title{position:absolute;left:0;top:114px;width:184px;text-align:center;color:var(--white);font-size:11px;font-weight:700;line-height:18px}
.author-title em{font-weight:400;font-size:10px}
.popular{position:absolute;left:0;top:155px;width:184px;height:224px;background:var(--side-dark);padding:12px 14px 0}
.popular h2{font-size:11px;font-weight:700;color:var(--white);padding-bottom:5px;border-bottom:2px solid #ddd;display:flex;align-items:center;gap:6px}
.popular h2 .icon{width:14px;height:16px;background:var(--orange)}
.post{display:flex;gap:5px;padding:6px 0;border-bottom:1px solid #555}
.post:last-child{border-bottom:0}
.post-thumb{width:48px;height:48px;flex:none;background:linear-gradient(135deg,#8a6a3a,#3a3a2a)}
.post-title{font-size:8.5px;font-weight:700;color:var(--white);line-height:10px;text-transform:uppercase}
.post-meta{font-size:8px;color:var(--muted);margin-top:3px;line-height:13px}
.post-meta b{font-weight:400;color:var(--orange)}
.site-footer{position:absolute;left:0;top:674px;width:1200px;height:128px;background:var(--footer);color:var(--white)}
.site-footer h3{font-size:12.5px;font-weight:700;font-variant:small-caps;border-bottom:1px solid var(--white);display:inline-block;padding-bottom:1px}
.quick{position:absolute;left:239px;top:16px}
.quick ul{list-style:none;margin-top:5px}
.quick li{font-size:9px;line-height:15px}
.newsletter{position:absolute;left:537px;top:16px;width:130px}
.newsletter h3{font-size:10.5px}
.newsletter p{font-size:8px;line-height:10px;margin-top:6px}
.newsletter .field{margin-top:6px;width:126px;height:18px;border:1px solid #bbb;font-size:8px;color:#bbb;padding:4px 7px}
.newsletter .submit{margin-top:7px;width:57px;height:18px;background:var(--orange);font-size:6.5px;text-align:center;line-height:18px;text-transform:uppercase}
.follow{position:absolute;left:893px;top:14px}
.follow h3{font-size:10.5px}
.social{display:flex;gap:7px;margin-top:6px}
.social span{width:18px;height:18px;background:var(--orange)}
</style>
</head>
<body>
<div class="hero-photo" role="img" aria-label="Close-up photograph of a full dark beard"></div>
<div class="beard-photo" role="img" aria-label="Photograph of a bearded man's chin and grey jacket"></div>

<div class="brand"><span class="brand-mark"></span><span class="brand-name">Top Whisker Tonic</span></div>

<nav class="main-nav">
  <a class="active" href="#" style="left:328px">Home</a>
  <a href="#" style="left:415px">Review Methodology</a>
  <a class="hover" href="#" style="left:612px">Charter</a>
  <a href="#" style="left:717px">Blog</a>
  <a href="#" style="left:798px">About Me</a>
</nav>

<section class="review-panel">
  <h1>The World’s #1 Beard Oil Authority</h1>
  <p class="intro">Here is the master list of beard oils reviewed to date. You can link directly to the corresponding review by clicking on the name of the beard oil. In accordance with our charter, we are actively working to locate and review every single beard oil available on the planet Earth, so check back regularly for updates.</p>
  <table class="compare">
    <colgroup><col style="width:51px"><col style="width:52px"><col style="width:28px"><col style="width:52px"><col style="width:40px"><col style="width:42px"><col style="width:43px"><col style="width:45px"><col style="width:40px"><col style="width:45px"><col style="width:72px"></colgroup>
    <thead><tr><th>Suplier</th><th>Name</th><th>Oil</th><th>Country of Origin</th><th>Aroma</th><th>Grease</th><th>Condition</th><th>Delivery</th><th>Value</th><th>Overallt</th><th>Link</th></tr></thead>
    <tbody>
      <tr><td class="txt">Northfold Beard Co.</td><td class="txt">Timberline</td><td><span class="bottle" role="img" aria-label="Oil bottle"></span></td><td>Australia</td><td class="num">7</td><td class="num">5</td><td class="num">3</td><td class="num">5</td><td class="num">6</td><td class="num">7</td><td><span class="buy">Get yours now</span></td></tr>
      <tr><td class="txt">Papa Renn Grooming</td><td class="txt">Hazy Ridge Beard Oil</td><td><span class="bottle dark" role="img" aria-label="Oil bottle"></span></td><td>Australia</td><td class="num">8</td><td class="num">8</td><td class="num">8</td><td class="num">8</td><td class="num">6</td><td class="num">8</td><td><span class="buy">Get yours now</span></td></tr>
      <tr><td class="txt">Bristled Rogue</td><td class="txt">Pinecutter</td><td><span class="bottle pale" role="img" aria-label="Oil bottle"></span></td><td>USA</td><td class="num">7</td><td class="num">5</td><td class="num">1</td><td class="num">5</td><td class="num">3</td><td class="num">6</td><td><span class="buy">Get yours now</span></td></tr>
      <tr><td class="txt">Barvok Men's Grooming</td><td class="txt">Barvok Beard Oil</td><td><span class="bottle dark" role="img" aria-label="Oil bottle"></span></td><td>Australia</td><td class="num">7</td><td class="num">3</td><td class="num">7</td><td class="num">8</td><td class="num">10</td><td class="num">8</td><td><span class="buy">Get yours now</span></td></tr>
      <tr><td class="txt">Everskin Soaps</td><td class="txt">Scrubland Beard Oil</td><td><span class="bottle dark" role="img" aria-label="Oil bottle"></span></td><td>Australia</td><td class="num">7</td><td class="num">5</td><td class="num">8</td><td class="num">8</td><td class="num">5</td><td class="num">7</td><td><span class="buy">Get yours now</span></td></tr>
    </tbody>
  </table>
</section>

<aside class="sidebar">
  <div class="author-photo" role="img" aria-label="Round portrait photo of the reviewer Delvin Marsk"></div>
  <p class="author-title">Global Beard Oil Reviews<br><em>- by Delvin Marsk</em></p>
  <div class="popular">
    <h2><span class="icon"></span>Popular Posts</h2>
    <div class="post"><div class="post-thumb" role="img" aria-label="Beard oil product photo"></div><div><p class="post-title">Hazy Ridge Beard Oil Papa ...</p><p class="post-meta">BY: <b>Delvin Marsk</b><br>February 12, 2016</p></div></div>
    <div class="post"><div class="post-thumb" role="img" aria-label="Beard oil product photo"></div><div><p class="post-title">Scrubland Face/Beard Oil by Everskin ...</p><p class="post-meta">BY: <b>Delvin Marsk</b><br>February 09, 2016</p></div></div>
    <div class="post"><div class="post-thumb" role="img" aria-label="Beard oil product photo"></div><div><p class="post-title">Barvok Beard Oil by Barvok ...</p><p class="post-meta">BY: <b>Delvin Marsk</b><br>January 25, 2016</p></div></div>
  </div>
</aside>

<footer class="site-footer">
  <div class="quick"><h3>Quick Links</h3>
    <ul><li>Home</li><li>Review Methedology</li><li>Charter</li><li>Blog</li><li>About Me</li></ul></div>
  <div class="newsletter"><h3>Subscribe to my newsletter</h3>
    <p>Don’t miss out on any of my reviews and offers.</p>
    <div class="field">Enter your email here</div>
    <div class="submit">Submit</div></div>
  <div class="follow"><h3>Follow me on</h3>
    <div class="social"><span aria-label="Social link"></span><span aria-label="Social link"></span><span aria-label="Social link"></span></div></div>
</footer>
</body>
</html>
```